Print materials for 3-star hotel

We are changing up our print materials (notepads, letterheads, key card jackets, small flyer for the room rates) We are a 3 star business hotel in the Philippines and have mainly used grey tones and clean, simple lines. See attached photos for logo and hotel interior photos.

Target Market(s)

Business

Contact Information for Business Card

Corvale Terrace Hotel
Lindwell Banca Avenue corner Tolenta St Cebu City 6000 Philippines
Tel: +63 32 481 7302
Mobile: +63 917 648 2095
www.corvaleterracehotel.example

Font styles to use
Serif
Sans Serif

Requirements
Must have
• Simple
• Readable font and font size
Nice to have
• Neutral colors, grey and taupes
Should not have
• No purples and bright blues

```html
<!DOCTYPE html>
<html lang="en">
<head>
<meta charset="utf-8">
<title>Corvale Terrace Hotel – Stationery</title>
<link rel="stylesheet" href="https://fonts.googleapis.com/css2?family=Cinzel:wght@400&family=Raleway:wght@400;500&family=Roboto:wght@400;700&display=swap">
<style>
  :root {
    --backdrop: #dcdcdc;
    --paper: #f3f3f3;
    --paper-white: #fafafa;
    --ink: #000000;
    --charcoal: #1b1b1b;
    --folder: #1e1e1e;
    --folder-edge: #111111;
    --grey-band: #b3b3b3;
    --body-text: #6a6a6a;
    --signature: #a9b6c6;
  }
  * { margin: 0; padding: 0; box-sizing: border-box; }
  html, body { width: 1200px; height: 899px; overflow: hidden; }
  body { background: var(--backdrop); position: relative; font-family: "Raleway", sans-serif; }

  .piece { position: absolute; overflow: hidden; }

  /* wordmark */
  .wordmark { display: flex; flex-direction: column; align-items: center; font-family: "Cinzel", serif; font-weight: 400; color: var(--ink); text-align: center; line-height: 1.2; }
  .wordmark .mark-square { background: currentColor; margin-bottom: 4px; }
  .wordmark .name, .wordmark .sub { letter-spacing: 0.18em; }
  .wordmark.light { color: #ffffff; }

  /* letterhead */
  .letterhead { left: 152px; top: 80px; width: 378px; height: 532px; background: var(--paper); }
  .letterhead .wordmark { position: absolute; top: 34px; left: 0; right: 0; }
  .letterhead .mark-square { width: 18px; height: 18px; }
  .letterhead .name, .letterhead .sub { font-size: 7.5px; }
  .letter-body { position: absolute; left: 34px; top: 150px; width: 312px; color: var(--body-text); }
  .greeting { font-size: 9.5px; color: #444; margin-bottom: 14px; }
  .letter-body p { font-size: 5.2px; line-height: 8.2px; margin-bottom: 8px; text-align: justify; }
  .letter-body .closing { margin-top: 14px; }
  .signature { width: 70px; height: 26px; background: var(--signature); opacity: .55; border-radius: 3px; margin-top: 10px; }
  .footer-band { position: absolute; left: 0; top: 498px; height: 22px; width: 378px; }
  .footer-band .black { position: absolute; left: 0; top: 0; width: 316px; height: 22px; background: var(--ink); color: #fff; font-family: "Roboto", sans-serif; font-size: 5.2px; text-align: center; padding-top: 5px; line-height: 7px; }
  .footer-band .black b { font-weight: 700; }
  .footer-band .square { position: absolute; left: 323px; top: 3px; width: 16px; height: 16px; background: var(--ink); }
  .footer-band .grey { position: absolute; left: 332px; top: 0; width: 46px; height: 22px; background: var(--grey-band); }
  .footer-band .square { z-index: 1; }

  /* folder */
  .folder { left: 564px; top: 48px; width: 445px; height: 565px; background: var(--folder); }
  .folder .spine { position: absolute; top: 0; bottom: 0; width: 1px; background: var(--folder-edge); }
  .folder .wordmark { position: absolute; left: 0; right: 0; top: 232px; padding-left: 10px; }
  .folder .mark-square { width: 48px; height: 48px; margin-bottom: 10px; }
  .folder .name { font-size: 17px; letter-spacing: 0.2em; }
  .folder .sub { font-size: 12px; letter-spacing: 0.3em; }

  /* business cards */
  .card-front { left: 67px; top: 656px; width: 157px; height: 90px; background: var(--charcoal); }
  .card-front .wordmark { position: absolute; left: 0; right: 0; top: 30px; }
  .card-front .mark-square { width: 13px; height: 13px; }
  .card-front .name, .card-front .sub { font-size: 5.6px; }
  .card-front .web { position: absolute; left: 0; right: 0; bottom: 10px; text-align: center; font-size: 3.6px; letter-spacing: .2em; color: #bbb; }

  .card-back { left: 67px; top: 762px; width: 157px; height: 91px; background: var(--paper-white); }
  .card-back .wordmark { position: absolute; left: 8px; top: 11px; width: 62px; }
  .card-back .mark-square { width: 11px; height: 11px; margin-bottom: 3px; }
  .card-back .name, .card-back .sub { font-size: 4.8px; }
  .card-back .person { position: absolute; right: 13px; top: 17px; text-align: right; font-family: "Roboto", sans-serif; color: var(--ink); }
  .card-back .person .who { font-size: 5.6px; font-weight: 700; }
  .card-back .person .role { font-size: 3.8px; }
  .card-back .band { position: absolute; left: 0; top: 42px; width: 107px; height: 43px; background: var(--ink); color: #fff; font-family: "Roboto", sans-serif; font-size: 3.5px; line-height: 4.8px; padding: 6px 0 0 10px; }
  .card-back .band .gap { height: 3px; }
  .card-back .block { position: absolute; left: 107px; top: 42px; width: 50px; height: 43px; background: var(--grey-band); }
  .card-back .block .square { position: absolute; left: 8px; top: 6px; width: 24px; height: 31px; background: var(--ink); }

  /* compliment slip */
  .slip { left: 242px; top: 656px; width: 436px; height: 198px; background: var(--paper-white); }
  .slip .wordmark { position: absolute; left: 24px; top: 26px; width: 78px; }
  .slip .mark-square { width: 18px; height: 18px; }
  .slip .name, .slip .sub { font-size: 7px; }
  .slip .band { position: absolute; left: 0; top: 163px; width: 374px; height: 23px; background: var(--ink); color: #fff; font-family: "Roboto", sans-serif; font-size: 6px; line-height: 8px; padding: 4px 0 0 27px; }
  .slip .grey { position: absolute; left: 398px; top: 163px; width: 38px; height: 23px; background: var(--grey-band); }
  .slip .square { position: absolute; left: 377px; top: 163px; width: 18px; height: 23px; background: var(--ink); }

  /* envelope */
  .envelope { left: 700px; top: 654px; width: 436px; height: 198px; background: var(--paper); }
  .envelope .flap { position: absolute; left: 0; top: 0; width: 436px; height: 62px; }
  .envelope .wordmark { position: absolute; left: 0; right: 0; top: 14px; }
  .envelope .mark-square { width: 18px; height: 18px; margin-bottom: 3px; }
  .envelope .name { font-size: 6.5px; }
</style>
</head>
<body>

  <!-- Letterhead -->
  <section class="piece letterhead">
    <div class="wordmark">
      <span class="mark-square"></span>
      <span class="name">Corvale Terrace</span>
      <span class="sub">Hotel</span>
    </div>
    <div class="letter-body">
      <div class="greeting">Dear Mr. Dalton,</div>
      <p>Thank you for choosing our hotel for your upcoming stay in Cebu City. We are pleased to confirm your reservation for a deluxe room with city view, including daily breakfast for two guests, free wireless internet throughout the property and access to our business centre on the second floor of the main building.</p>
      <p>Check-in begins at two in the afternoon and check-out is at noon. Should you need an early arrival or a late departure, please let our front desk know in advance and we will do our best to arrange it. Airport transfers can be booked at a fixed rate with one day of notice.</p>
      <p>Our meeting rooms seat up to forty people and come with a projector, sound system and coffee service. Corporate guests staying three nights or more receive pressing for two garments each day and a welcome drink at the lobby lounge. Parking is free for registered guests, and our concierge can help with dinner bookings, local tours and printing.</p>
      <p>We look forward to welcoming you and making your business trip comfortable and productive. If anything changes in your plans, simply reply to this letter or call our reservations team at any hour.</p>
      <p class="closing">Sincerely,</p>
      <div class="signature" role="img" aria-label="Handwritten signature of Elena Marquez"></div>
    </div>
    <div class="footer-band">
      <div class="black">
        Lindwell Banca Avenue corner Tolenta St, Cebu City 6000 | <b>P:</b> +63 32 481 7302<br>
        <b>M:</b> +63 917 648 2095 &nbsp;<b>F:</b> +63 32 481 7310 &nbsp;<b>E:</b> stay@corvaleterracehotel.example &nbsp;<b>W:</b> www.corvaleterracehotel.example
      </div>
      <div class="grey"></div>
      <div class="square"></div>
    </div>
  </section>

  <!-- Presentation folder -->
  <section class="piece folder">
    <span class="spine" style="left:6px"></span>
    <span class="spine" style="left:14px"></span>
    <span class="spine" style="left:24px"></span>
    <div class="wordmark light">
      <span class="mark-square"></span>
      <span class="name">Corvale Terrace</span>
      <span class="sub">Hotel</span>
    </div>
  </section>

  <!-- Business card, front -->
  <section class="piece card-front">
    <div class="wordmark light">
      <span class="mark-square"></span>
      <span class="name">Corvale Terrace</span>
      <span class="sub">Hotel</span>
    </div>
    <div class="web">www.corvaleterracehotel.example</div>
  </section>

  <!-- Business card, back -->
  <section class="piece card-back">
    <div class="wordmark">
      <span class="mark-square"></span>
      <span class="name">Corvale Terrace</span>
      <span class="sub">Hotel</span>
    </div>
    <div class="person">
      <div class="who">ELENA MARQUEZ</div>
      <div class="role">CEO/FOUNDER</div>
    </div>
    <div class="band">
      Lindwell Banca Avenue corner Tolenta St<br>
      Cebu City 6000 Philippines
      <div class="gap"></div>
      Tel: +63 32 481 7302<br>
      Mob: +63 917 648 2095<br>
      www.corvaleterracehotel.example
    </div>
    <div class="block"><span class="square"></span></div>
  </section>

  <!-- Compliment slip -->
  <section class="piece slip">
    <div class="wordmark">
      <span class="mark-square"></span>
      <span class="name">Corvale Terrace</span>
      <span class="sub">Hotel</span>
    </div>
    <div class="band">PO Box 318 Cebu City<br>Cebu 6000 Philippines</div>
    <div class="square"></div>
    <div class="grey"></div>
  </section>

  <!-- Envelope -->
  <section class="piece envelope">
    <svg class="flap" viewBox="0 0 436 62" aria-hidden="true">
      <path d="M0 0 H436 V12 Q436 24 426 34 Q410 62 380 62 H56 Q26 62 10 34 Q0 24 0 12 Z" fill="var(--ink)"/>
    </svg>
    <div class="wordmark light">
      <span class="mark-square"></span>
      <span class="name">Corvale Terrace Hotel</span>
    </div>
  </section>

</body>
</html>
```